Business Card Design for Varomir Facility Services

We are looking for a Business Card Design for the Company "Varomir Facility Services."
Front side:
- Company Logo (small)
- Company Name, address, pohone, website and personal data.
- white background, for text e.g. company colors (blue or green like in the logo)
Please use following data:
Company data:
Varomir Facility Services Kostelac
Birkenhaldweg 14
6330 Cham
www.varomir-fs.ch
Person data:
Tarik Kostelac
Geschäftsführer
+41 76 519 47 83
info@varomir-fs.ch
Back side:
could be colored in blue or green
please use a big logo sing and some smaller icons to say what is all beeing offered in facility services, like cleaning, maintenance cleaning
industrial cleaning, caretaking, gardening, disposal. There is no need for everyone of the icons if there are similar or an icon is standing for more of them.
colors to use:
blue: HEX 246BB0
green: HEX 52B33E

```html
<!DOCTYPE html>
<html lang="de">
<head>
<meta charset="utf-8">
<title>Varomir Facility Services – Visitenkarte</title>
<link rel="stylesheet" href="https://fonts.googleapis.com/css2?family=Source+Sans+3:wght@400;600&display=swap">
<style>
  :root {
    --brand-blue: #1668b2;
    --ink: #1b1f24;
    --ink-soft: #3a3f45;
    --paper: #ffffff;
    --page: #ffffff;
  }
  * { box-sizing: border-box; margin: 0; padding: 0; }
  html, body {
    width: 1200px; height: 960px; overflow: hidden;
    background: var(--page);
    font-family: "Source Sans 3", "Source Sans Pro", sans-serif;
  }
  .canvas { position: relative; width: 1200px; height: 960px; }

  .card {
    position: absolute;
    left: 286px; width: 629px; height: 360px;
    background: var(--paper);
    box-shadow: 0 2px 6px rgba(0,0,0,0.28);
    overflow: hidden;
  }
  .card--front { top: 109px; }
  .card--back { top: 492px; }

  /* Front */
  .front__band {
    position: absolute; left: 0; top: 0; width: 202px; height: 100%;
    background: var(--brand-blue);
  }
  .front__brand {
    position: absolute; left: 101px; top: 180px;
    transform: translate(-50%, -50%) rotate(-90deg);
    white-space: nowrap;
    color: var(--paper);
    font-weight: 600; font-size: 26px; letter-spacing: 1px;
  }
  .person { position: absolute; left: 246px; top: 91px; }
  .person__name { font-weight: 600; font-size: 24px; color: var(--ink); line-height: 1.2; }
  .person__role { font-size: 18px; color: var(--ink); margin-top: 2px; }
  .contact { position: absolute; left: 245px; top: 164px; list-style: none; }
  .contact__item {
    display: flex; align-items: center; height: 26.4px;
    font-size: 17px; color: var(--ink);
  }
  .contact__icon { width: 17px; height: 17px; margin-right: 15px; fill: var(--brand-blue); }

  /* Back */
  .back__brand {
    position: absolute; left: 0; right: 0; top: 128px;
    text-align: center; color: var(--brand-blue); font-weight: 600;
  }
  .back__brand-name { font-size: 52px; letter-spacing: 4px; line-height: 1; }
  .back__brand-sub { font-size: 19px; letter-spacing: 4px; margin-top: 6px; }
  .services { position: absolute; top: 264px; left: 0; width: 100%; height: 60px; }
  .services__col { position: absolute; top: 0; list-style: none; }
  .services__col--1 { left: 40px; }
  .services__col--2 { left: 273px; }
  .services__col--3 { left: 484px; }
  .services__item {
    display: flex; align-items: center; height: 26.4px;
    font-size: 18px; color: var(--ink-soft);
  }
  .services__star { width: 16px; height: 16px; margin-right: 15px; fill: var(--brand-blue); }
  .back__band {
    position: absolute; left: 0; bottom: 0; width: 100%; height: 23px;
    background: var(--brand-blue);
  }
</style>
</head>
<body>
<svg width="0" height="0" style="position:absolute">
  <defs>
    <symbol id="icon-star" viewBox="0 0 20 20">
      <path d="M10 0 L11.6 8.4 L20 10 L11.6 11.6 L10 20 L8.4 11.6 L0 10 L8.4 8.4 Z" transform="rotate(15 10 10)"/>
    </symbol>
  </defs>
</svg>
<div class="canvas">

  <section class="card card--front">
    <div class="front__band">
      <div class="front__brand">Varomir Facility Services</div>
    </div>
    <div class="person">
      <div class="person__name">Tarik Kostelac</div>
      <div class="person__role">Geschäftsführer</div>
    </div>
    <ul class="contact">
      <li class="contact__item">
        <svg class="contact__icon" viewBox="0 0 24 24"><path d="M6.6 10.8a15.1 15.1 0 0 0 6.6 6.6l2.2-2.2c.3-.3.7-.4 1-.2 1.1.4 2.3.6 3.6.6.6 0 1 .4 1 1V20c0 .6-.4 1-1 1C10.6 21 3 13.4 3 4c0-.6.4-1 1-1h3.5c.6 0 1 .4 1 1 0 1.3.2 2.5.6 3.6.1.3 0 .7-.2 1z"/></svg>
        +41 76 519 47 83
      </li>
      <li class="contact__item">
        <svg class="contact__icon" viewBox="0 0 24 24"><path d="M2 5h20v14H2z M4 7v.5l8 5.5 8-5.5V7l-8 5.5z" fill-rule="evenodd"/></svg>
        info@varomir-fs.ch
      </li>
      <li class="contact__item">
        <svg class="contact__icon" viewBox="0 0 24 24"><path d="M12 2a10 10 0 1 0 0 20 10 10 0 0 0 0-20zm0 2c1.2 0 2.6 2.5 3 7H9c.4-4.5 1.8-7 3-7zm-8 8.9h3a17 17 0 0 0 1.5 6.2A8 8 0 0 1 4 12.9zm0-1.9a8 8 0 0 1 4.5-6.2A17 17 0 0 0 7 11zm8 9c-1.2 0-2.6-2.5-3-7h6c-.4 4.5-1.8 7-3 7zm3.5-.9a17 17 0 0 0 1.5-6.2h3a8 8 0 0 1-4.5 6.2zM17 11a17 17 0 0 0-1.5-6.2A8 8 0 0 1 20 11z"/></svg>
        www.varomir-fs.ch
      </li>
      <li class="contact__item">
        <svg class="contact__icon" viewBox="0 0 24 24"><path d="M12 1a6.5 6.5 0 0 0-6.5 6.5C5.5 12.4 12 19 12 19s6.5-6.6 6.5-11.5A6.5 6.5 0 0 0 12 1zm0 9a2.5 2.5 0 1 1 0-5 2.5 2.5 0 0 1 0 5z"/><ellipse cx="12" cy="21" rx="7" ry="2" fill="none" stroke="#1668b2" stroke-width="1.5"/></svg>
        Birkenhaldweg 14, 6330 Cham
      </li>
    </ul>
  </section>

  <section class="card card--back">
    <div class="back__brand">
      <div class="back__brand-name">VAROMIR</div>
      <div class="back__brand-sub">FACILITY SERVICES</div>
    </div>
    <div class="services">
      <ul class="services__col services__col--1">
        <li class="services__item"><svg class="services__star"><use href="#icon-star"/></svg>Like cleaning</li>
        <li class="services__item"><svg class="services__star"><use href="#icon-star"/></svg>Maintenance cleaning</li>
      </ul>
      <ul class="services__col services__col--2">
        <li class="services__item"><svg class="services__star"><use href="#icon-star"/></svg>Industrial cleaning</li>
        <li class="services__item"><svg class="services__star"><use href="#icon-star"/></svg>Caretaking</li>
      </ul>
      <ul class="services__col services__col--3">
        <li class="services__item"><svg class="services__star"><use href="#icon-star"/></svg>Gardening</li>
        <li class="services__item"><svg class="services__star"><use href="#icon-star"/></svg>Disposal</li>
      </ul>
    </div>
    <div class="back__band"></div>
  </section>

</div>
</body>
</html>
```